web page look and feel - B2B enterprise application

We have an enterprise application with 10 to 15 core pages and several supporting pages or popups. To start, we want the graphical design of the Users, Roles and Data Source pages and their supporting popups, wizards, etc. to be made beautiful. That is around 10 pages in total. There is a fair amount of redundancy among the pages. I have attached 5 screenshots. We very much want the pages to project a premium feel. That is absolutely essential. The color scheme is blue and sometimes yellow (only if it makes the page look better) plus black, gray and white. If the design of these screens goes well, we would expand the project to continue with other pages. The core of what we are looking for is graphic in nature but we are open to workflow suggestions if you have them. The Roles screen needs some improvements to the layout. I am looking for everything that includes icons, fonts, spacing, etc. I assume getting to the final design will take some back and forth with multiple revisions.

Target Market(s)

Large Enterprises

Number of Pages Required

5+ page

Requirements
Must have
• Premium feel

```html
<!DOCTYPE html>
<html lang="en">
<head>
<meta charset="utf-8">
<title>Lumora Data – Roles</title>
<link href="https://fonts.googleapis.com/css2?family=Mulish:wght@400;500;600&display=swap" rel="stylesheet">
<style>
:root{
  --blue:#2c6eae;
  --blue-dark:#245e97;
  --side:#2b2c31;
  --yellow:#f1b620;
  --text:#3b3b3b;
  --muted:#666;
  --line:#dcdcdc;
  --white:#fff;
}
*{box-sizing:border-box;margin:0;padding:0}
html,body{width:1200px;height:818px;overflow:hidden;background:var(--white);font-family:'Mulish',sans-serif;color:var(--text)}
.topbar{position:absolute;left:0;top:0;width:1200px;height:62px;background:var(--blue);color:var(--white)}
.brand{position:absolute;left:42px;top:17px;display:flex;align-items:center;gap:10px;font-size:20px;font-weight:500}
.brand-dot{width:16px;height:16px;border-radius:50%;background:var(--white)}
.menu-toggle{position:absolute;left:241px;top:21px}
.tool-icons{position:absolute;left:845px;top:20px;display:flex;gap:22px}
.user-menu{position:absolute;left:1077px;top:21px;font-size:16px;display:flex;align-items:center;gap:8px}
.sidebar{position:absolute;left:0;top:62px;width:261px;height:638px;background:var(--side);color:var(--white)}
.nav{list-style:none;position:absolute;left:0;top:55px;width:100%}
.nav li{height:39.2px;display:flex;align-items:center;font-size:13px;position:relative;padding-left:70px}
.nav svg{position:absolute;left:38px}
.page-title{position:absolute;left:282px;top:115px;font-size:26px;font-weight:500;color:#333}
.btn-add{position:absolute;left:373px;top:115px;width:57px;height:31px;background:var(--blue);color:var(--white);border-radius:3px;font-size:14px;font-weight:500;display:flex;align-items:center;justify-content:center}
.search{position:absolute;left:826px;top:114px;width:334px;height:40px;border:1px solid #e8e8e8;background:#fdfdfd}
.search-btn{position:absolute;right:-1px;top:-1px;width:43px;height:40px;background:var(--yellow);display:flex;align-items:center;justify-content:center}
.adv-search{position:absolute;right:40px;top:168px;font-size:13px;color:var(--blue)}
.panel{position:absolute;left:283px;top:213px;width:877px;height:487px;border:1px solid var(--line)}
table{border-collapse:collapse;table-layout:fixed;width:876px;font-size:10.5px}
th{height:38px;font-weight:400;font-size:12px;color:#444;border-right:1px solid var(--line);border-bottom:1px solid var(--line);white-space:nowrap}
th.role{background:var(--blue);color:var(--white);text-align:left;padding-left:12px}
th.role svg{margin-left:10px;vertical-align:middle}
td{height:45.6px;border-right:1px solid var(--line);border-bottom:1px solid var(--line);text-align:center;color:#555}
td.name{text-align:left;padding-left:12px;font-size:12px;color:#444}
.perm{display:flex;flex-direction:column;align-items:center;gap:3px}
.perm span,.inline span{display:inline-flex;align-items:center;gap:2px}
.perm.two{align-items:flex-start;display:inline-flex}
.inline{display:flex;justify-content:center;gap:6px}
svg.c{width:9px;height:9px;color:var(--blue)}
td.act{background:var(--blue);border-right:1px solid #4c86be}
td.act svg{width:11px;height:11px;color:var(--white)}
td.empty{border-right:none}
.pager{position:absolute;left:586px;top:520px;display:flex;align-items:center}
.pg{width:14px;display:flex;justify-content:center;color:#555}
.pg-current{width:35px;height:27px;background:var(--blue);color:var(--white);border-radius:2px;display:flex;align-items:center;justify-content:center;font-size:13px;font-weight:600}
.pg-size{width:35px;height:27px;background:var(--yellow);color:var(--white);border-radius:2px;display:flex;align-items:center;justify-content:center;font-size:13px;font-weight:600}
.footer{position:absolute;left:0;width:100%;top:746px;padding-left:90px;text-align:center;font-size:12.5px;color:#666}
</style>
</head>
<body>
<svg width="0" height="0" style="position:absolute">
  <symbol id="chk" viewBox="0 0 10 10"><rect x="0.7" y="1.7" width="7.6" height="7.6" rx="1.3" fill="none" stroke="currentColor" stroke-width="1.2"/><path d="M2.6 5.2 4.4 7 9.3 1.5" fill="none" stroke="currentColor" stroke-width="1.4"/></symbol>
  <symbol id="box" viewBox="0 0 10 10"><rect x="0.7" y="1.7" width="7.6" height="7.6" rx="1.3" fill="none" stroke="currentColor" stroke-width="1.2"/></symbol>
  <symbol id="copy" viewBox="0 0 12 12"><rect x="1" y="3.5" width="6.5" height="7.5" rx="1" fill="none" stroke="currentColor" stroke-width="1.3"/><path d="M4.5 3.5V1h6.5v7.5H7.5" fill="none" stroke="currentColor" stroke-width="1.3"/></symbol>
  <symbol id="edit" viewBox="0 0 12 12"><rect x="1" y="2" width="8" height="9" rx="1" fill="none" stroke="currentColor" stroke-width="1.3"/><path d="M4.5 7.5 5 6 10.5 0.8 11.4 1.7 6 7Z" fill="currentColor"/></symbol>
  <symbol id="trash" viewBox="0 0 12 12"><path d="M2 3h8M4.5 3V1.5h3V3M3 3l.6 8h4.8L9 3M5 5v4M7 5v4" fill="none" stroke="currentColor" stroke-width="1.2"/></symbol>
</svg>

<header class="topbar">
  <div class="brand"><span class="brand-dot"></span>Lumora Data</div>
  <svg class="menu-toggle" width="20" height="18" viewBox="0 0 20 18"><path d="M0 2h20M0 9h20M0 16h20" stroke="#fff" stroke-width="3"/></svg>
  <div class="tool-icons">
  <svg width="22" height="20" viewBox="0 0 22 20"><path d="M2 17a9 9 0 1 1 18 0z" fill="#fff"/><circle cx="11" cy="15" r="2" fill="#2c6eae"/><path d="M11 15 15 8" stroke="#2c6eae" stroke-width="2"/></svg>
  <svg width="22" height="22" viewBox="0 0 22 22"><path d="M2 20 15 7" stroke="#fff" stroke-width="3"/><path d="M17 1v4M15 3h4M20 8v3M18.5 9.5h3" stroke="#fff" stroke-width="1.5"/></svg>
  <svg width="20" height="20" viewBox="0 0 20 20"><circle cx="10" cy="10" r="10" fill="#fff"/><path d="M7 7.5a3 3 0 1 1 4 2.8c-1 .4-1 1-1 2" fill="none" stroke="#2c6eae" stroke-width="2.2"/><circle cx="10" cy="15.5" r="1.3" fill="#2c6eae"/></svg>
  <svg width="20" height="20" viewBox="0 0 20 20"><g fill="#fff"><circle cx="10" cy="10" r="6.5"/><rect x="8" y="0.5" width="4" height="19" rx="1"/><rect x="0.5" y="8" width="19" height="4" rx="1"/><rect x="8" y="0.5" width="4" height="19" rx="1" transform="rotate(45 10 10)"/><rect x="8" y="0.5" width="4" height="19" rx="1" transform="rotate(-45 10 10)"/></g><circle cx="10" cy="10" r="2.8" fill="#2c6eae"/></svg>
  </div>
  <div class="user-menu">Dana Moore <svg width="10" height="6" viewBox="0 0 10 6"><path d="M1 1l4 4 4-4" fill="none" stroke="#fff" stroke-width="1.6"/></svg></div>
</header>

<aside class="sidebar">
  <ul class="nav">
    <li><svg width="14" height="12" viewBox="0 0 14 12"><circle cx="7" cy="3.5" r="2.5" fill="#fff"/><circle cx="2.5" cy="4" r="1.8" fill="#fff"/><circle cx="11.5" cy="4" r="1.8" fill="#fff"/><path d="M2.5 12a4.5 4 0 0 1 9 0zM0 10a2.5 3 0 0 1 3-3M14 10a2.5 3 0 0 0-3-3" fill="#fff"/></svg>Users</li>
    <li>Roles</li>
    <li>Notification Groups</li>
    <li><svg width="12" height="13" viewBox="0 0 12 13"><ellipse cx="6" cy="2.5" rx="5.5" ry="2.2" fill="#fff"/><path d="M.5 4.5c0 2.9 11 2.9 11 0v2c0 2.9-11 2.9-11 0zM.5 8.5c0 2.9 11 2.9 11 0v2c0 2.9-11 2.9-11 0z" fill="#fff"/></svg>Data Sources</li>
    <li><svg width="13" height="11" viewBox="0 0 13 11"><g fill="#fff"><rect width="3.5" height="3" /><rect x="4.7" width="3.5" height="3"/><rect x="9.4" width="3.5" height="3"/><rect y="4" width="3.5" height="3"/><rect x="4.7" y="4" width="3.5" height="3"/><rect x="9.4" y="4" width="3.5" height="3"/><rect y="8" width="3.5" height="3"/><rect x="4.7" y="8" width="3.5" height="3"/><rect x="9.4" y="8" width="3.5" height="3"/></g></svg>Data Object Relationships</li>
    <li><svg width="12" height="11" viewBox="0 0 12 11"><g fill="#fff"><rect width="5.3" height="5" rx="1"/><rect x="6.7" width="5.3" height="5" rx="1"/><rect y="6" width="5.3" height="5" rx="1"/><rect x="6.7" y="6" width="5.3" height="5" rx="1"/></g></svg>Data Sets</li>
    <li><svg width="12" height="11" viewBox="0 0 12 11"><path d="M2 1h10M0 4h12M2 7h10M0 10h12" stroke="#fff" stroke-width="2"/></svg>Rule Sets</li>
    <li><svg width="12" height="12" viewBox="0 0 12 12"><circle cx="6" cy="6" r="4.8" fill="none" stroke="#fff" stroke-width="1.8"/><path d="M6 3v3.3H8" fill="none" stroke="#fff" stroke-width="1.5"/></svg>Schedule</li>
    <li><svg width="14" height="11" viewBox="0 0 14 11"><path d="M3 9V3h8M11 2v6H3" fill="none" stroke="#fff" stroke-width="2"/><path d="M9 0l3 3-3 3zM5 5 2 8l3 3z" fill="#fff"/></svg>Metadata Import/Export</li>
    <li>Import</li>
    <li>Export</li>
  </ul>
</aside>

<main>
  <h1 class="page-title">Roles</h1>
  <div class="btn-add">ADD</div>
  <div class="search"><div class="search-btn"><svg width="14" height="14" viewBox="0 0 14 14"><circle cx="5.8" cy="5.8" r="4.3" fill="none" stroke="#fff" stroke-width="2.2"/><path d="M9 9l4 4" stroke="#fff" stroke-width="2.4"/></svg></div></div>
  <div class="adv-search">Advanced Search</div>

  <section class="panel">
    <table>
      <colgroup><col style="width:107px"><col style="width:86px"><col style="width:64px"><col style="width:63px"><col style="width:67px"><col style="width:101px"><col style="width:121px"><col style="width:135px"><col style="width:47px"><col style="width:28px"><col style="width:28px"><col style="width:29px"></colgroup>
      <thead><tr>
        <th class="role">Role Name<svg width="8" height="5" viewBox="0 0 8 5"><path d="M0 0h8L4 5z" fill="#fff"/></svg></th>
        <th>Data Sources</th><th>Data Sets</th><th>Rule Sets</th><th>Schedules</th><th>Suspect Matches</th><th>Master Data Objects</th><th>Metdata Import/Export</th><th>API</th><th colspan="3" class="empty"></th>
      </tr></thead>
      <tbody>
        <tr>
          <td class="name">System Admin</td>
          <td><div class="perm two"><span><svg class="c"><use href="#chk"/></svg>Read</span><span><svg class="c"><use href="#chk"/></svg>Write</span></div></td>
          <td><div class="perm two"><span><svg class="c"><use href="#chk"/></svg>Read</span><span><svg class="c"><use href="#box"/></svg>Write</span></div></td>
          <td><div class="perm two"><span><svg class="c"><use href="#chk"/></svg>Read</span><span><svg class="c"><use href="#chk"/></svg>Write</span></div></td>
          <td><div class="perm two"><span><svg class="c"><use href="#chk"/></svg>Read</span><span><svg class="c"><use href="#box"/></svg>Write</span></div></td>
          <td><div class="inline"><span><svg class="c"><use href="#chk"/></svg>Read</span><span><svg class="c"><use href="#chk"/></svg>Write</span></div></td>
          <td><div class="inline"><span><svg class="c"><use href="#chk"/></svg>Read</span><span><svg class="c"><use href="#chk"/></svg>Write</span></div></td>
          <td><div class="inline"><span><svg class="c"><use href="#chk"/></svg>Read</span><span><svg class="c"><use href="#box"/></svg>Write</span></div></td>
          <td><div class="perm two"><span><svg class="c"><use href="#chk"/></svg>Read</span><span><svg class="c"><use href="#box"/></svg>Write</span></div></td>
          <td class="act"><svg><use href="#copy"/></svg></td><td></td><td class="empty"></td>
        </tr>
        <tr>
          <td class="name">Role#1</td>
          <td><div class="perm two"><span><svg class="c"><use href="#chk"/></svg>Read</span><span><svg class="c"><use href="#chk"/></svg>Write</span></div></td>
          <td><div class="perm two"><span><svg class="c"><use href="#chk"/></svg>Read</span><span><svg class="c"><use href="#box"/></svg>Write</span></div></td>
          <td><div class="perm two"><span><svg class="c"><use href="#chk"/></svg>Read</span><span><svg class="c"><use href="#chk"/></svg>Write</span></div></td>
          <td><div class="perm two"><span><svg class="c"><use href="#chk"/></svg>Read</span><span><svg class="c"><use href="#box"/></svg>Write</span></div></td>
          <td><div class="inline"><span><svg class="c"><use href="#chk"/></svg>Read</span><span><svg class="c"><use href="#chk"/></svg>Write</span></div></td>
          <td><div class="inline"><span><svg class="c"><use href="#chk"/></svg>Read</span><span><svg class="c"><use href="#chk"/></svg>Write</span></div></td>
          <td><div class="inline"><span><svg class="c"><use href="#chk"/></svg>Read</span><span><svg class="c"><use href="#box"/></svg>Write</span></div></td>
          <td><div class="perm two"><span><svg class="c"><use href="#chk"/></svg>Read</span><span><svg class="c"><use href="#box"/></svg>Write</span></div></td>
          <td class="act"><svg><use href="#copy"/></svg></td><td></td><td class="empty"></td>
        </tr>
        <tr>
          <td class="name">Read Only</td>
          <td><div class="perm two"><span><svg class="c"><use href="#chk"/></svg>Read</span><span><svg class="c"><use href="#chk"/></svg>Write</span></div></td>
          <td><div class="perm two"><span><svg class="c"><use href="#chk"/></svg>Read</span><span><svg class="c"><use href="#box"/></svg>Write</span></div></td>
          <td><div class="perm two"><span><svg class="c"><use href="#chk"/></svg>Read</span><span><svg class="c"><use href="#chk"/></svg>Write</span></div></td>
          <td><div class="perm two"><span><svg class="c"><use href="#chk"/></svg>Read</span><span><svg class="c"><use href="#box"/></svg>Write</span></div></td>
          <td><div class="inline"><span><svg class="c"><use href="#chk"/></svg>Read</span><span><svg class="c"><use href="#chk"/></svg>Write</span></div></td>
          <td><div class="inline"><span><svg class="c"><use href="#chk"/></svg>Read</span><span><svg class="c"><use href="#chk"/></svg>Write</span></div></td>
          <td><div class="inline"><span><svg class="c"><use href="#chk"/></svg>Read</span><span><svg class="c"><use href="#box"/></svg>Write</span></div></td>
          <td><div class="perm two"><span><svg class="c"><use href="#chk"/></svg>Read</span><span><svg class="c"><use href="#box"/></svg>Write</span></div></td>
          <td class="act"><svg><use href="#edit"/></svg></td><td class="act"><svg><use href="#copy"/></svg></td><td class="act empty"><svg><use href="#trash"/></svg></td>
        </tr>
        <tr>
          <td class="name">Data Admin</td>
          <td><div class="perm two"><span><svg class="c"><use href="#chk"/></svg>Read</span><span><svg class="c"><use href="#chk"/></svg>Write</span></div></td>
          <td><div class="perm two"><span><svg class="c"><use href="#chk"/></svg>Read</span><span><svg class="c"><use href="#box"/></svg>Write</span></div></td>
          <td><div class="perm two"><span><svg class="c"><use href="#chk"/></svg>Read</span><span><svg class="c"><use href="#chk"/></svg>Write</span></div></td>
          <td><div class="perm two"><span><svg class="c"><use href="#chk"/></svg>Read</span><span><svg class="c"><use href="#box"/></svg>Write</span></div></td>
          <td><div class="inline"><span><svg class="c"><use href="#chk"/></svg>Read</span><span><svg class="c"><use href="#chk"/></svg>Write</span></div></td>
          <td><div class="inline"><span><svg class="c"><use href="#chk"/></svg>Read</span><span><svg class="c"><use href="#chk"/></svg>Write</span></div></td>
          <td><div class="inline"><span><svg class="c"><use href="#chk"/></svg>Read</span><span><svg class="c"><use href="#box"/></svg>Write</span></div></td>
          <td><div class="perm two"><span><svg class="c"><use href="#chk"/></svg>Read</span><span><svg class="c"><use href="#box"/></svg>Write</span></div></td>
          <td class="act"><svg><use href="#copy"/></svg></td><td></td><td class="empty"></td>
        </tr>
      </tbody>
    </table>
  </section>

  <nav class="pager">
    <span class="pg"><svg width="9" height="11" viewBox="0 0 9 11"><path d="M1 0v11" stroke="#555" stroke-width="2"/><path d="M9 0v11L2 5.5z" fill="#555"/></svg></span>
    <span style="width:18px"></span>
    <span class="pg"><svg width="12" height="11" viewBox="0 0 12 11"><path d="M6 0v11L0 5.5zM12 0v11L6 5.5z" fill="#555"/></svg></span>
    <span style="width:40px"></span>
    <span class="pg-current">1</span>
    <span style="width:42px"></span>
    <span class="pg"><svg width="12" height="11" viewBox="0 0 12 11"><path d="M0 0v11l6-5.5zM6 0v11l6-5.5z" fill="#555"/></svg></span>
    <span style="width:18px"></span>
    <span class="pg"><svg width="9" height="11" viewBox="0 0 9 11"><path d="M0 0v11l7-5.5z" fill="#555"/><path d="M8 0v11" stroke="#555" stroke-width="2"/></svg></span>
    <span style="width:45px"></span>
    <span class="pg-size">20</span>
  </nav>
</main>

<footer class="footer">Copyright 2018 Lumora Data.All Rights Reserved | Privacy Statement | Terms Of Use</footer>
</body>
</html>
```